Brisk Rainshield - Logo and Advert

Help to provide logo and advert.
Advert is to be short and concise to fit in a printed directory posted around homes.
Ideally the same advert to be able to be blown up as a leaflet.
Use of eco friendly type colours, soft greens and blues.
Logo to be subtle but indicative to roofing and facades.
Breakdown of advert as follows;
Company name:
Brisk Rainshield
Sub title:
Roofing & Façades
Services breakdown:
Pitched (Slating & Tiling)
Flat (Single Ply, Liquid & Mineral Felt)
Hard Metal (Zinc Standing Seam)
Leadwork
Roof lights and lanterns
Generic notes:
100% flame free applications available, eliminating all fire risks to your property. (No gas torch’s etc.).
Expert consultation and advice.
Product warranty and/or insurance backed warranty available.
Fully insured contractor.
Contact information:
Phone number to be confirmed
Email and/or website to be confirmed.
Please feel free to try out different colours and fonts other than outlined. I am not limited to those and open to suggestions.
Target Market(s)
Domestic/Private Home Owners/Small Buidlers
Industry/Entity Type
Roofing
Font styles to use
Look and feel
Each slider illustrates characteristics of the customer's brand and the style your logo design should communicate.

```html
<!DOCTYPE html>
<html lang="en">
<head>
<meta charset="utf-8">
<title>Brisk Rainshield – Roofing &amp; Façades Advert</title>
<link rel="stylesheet" href="https://fonts.googleapis.com/css2?family=Oswald:wght@400;500&family=Poppins:wght@400&display=swap">
<style>
  :root {
    --ink: #231f20;
    --blue: #0a8fd0;
    --green: #a6cf38;
    --paper: #ffffff;
    --text: #222222;
  }
  * { box-sizing: border-box; margin: 0; padding: 0; }
  html, body { width: 1200px; height: 1165px; overflow: hidden; background: var(--paper); }
  .advert { position: relative; width: 1200px; height: 1165px; font-family: "Poppins", sans-serif; color: var(--text); }
  .frame { position: absolute; inset: 0; }
  .abs { position: absolute; white-space: nowrap; line-height: 1; }

  .phone-icon { position: absolute; left: 50px; top: 40px; }
  .call-label { left: 160px; top: 43px; font-size: 33px; color: var(--green); }
  .call-number { left: 158px; top: 82px; font-size: 45px; color: var(--green); }

  .brand { left: 811px; width: 336px; text-align: center; }
  .brand-name { top: 83px; font-size: 35px; color: var(--blue); }
  .brand-sub { top: 131px; font-size: 25px; color: var(--green); }
  .brand-mark { position: absolute; left: 960px; top: 40px; width: 30px; height: 30px; background: var(--blue); }

  .services-title { left: 44px; top: 196px; font-family: "Oswald", sans-serif; font-weight: 500; font-size: 33px; color: var(--blue); }
  .services { position: absolute; left: 50px; top: 257px; list-style: none; }
  .services li { display: flex; align-items: center; height: 44.5px; font-size: 24px; }
  .services svg { margin-right: 8px; }

  .notes { position: absolute; left: 41px; top: 513px; font-size: 22px; color: var(--blue); line-height: 43.5px; }
  .notes p + p { margin-top: 9px; }

  .slogan { position: absolute; left: 41px; top: 810px; font-family: "Oswald", sans-serif; font-size: 48px; color: var(--green); line-height: 59px; }

  .photo { position: absolute; overflow: hidden; }
  .photo-label { position: absolute; bottom: 8px; left: 50%; transform: translateX(-50%); background: var(--green); color: var(--ink); font-size: 20px; padding: 4px 12px; white-space: nowrap; line-height: 1.1; }
  .photo-lead { left: 549px; top: 205px; width: 292px; height: 252px; background: linear-gradient(160deg, #8a9097, #4a4f55 55%, #d8d6c8); }
  .photo-membrane { left: 861px; top: 205px; width: 296px; height: 252px; background: linear-gradient(135deg, #e8ecef 0%, #cfd7de 40%, #4f86bd 60%, #2f6aa6 100%); }
  .photo-pitched { left: 549px; top: 474px; width: 297px; height: 252px; background: linear-gradient(170deg, #2f4a2e 0%, #6d7378 35%, #5a6066 60%, #9a5a44 100%); }
  .photo-lantern { left: 549px; top: 750px; width: 297px; height: 252px; background: linear-gradient(180deg, #3d7fc6 0%, #9cc2e6 40%, #4f5a66 70%, #8a8c8e 100%); }
  .photo-zinc { left: 865px; top: 474px; width: 296px; height: 530px; background: linear-gradient(100deg, #7d8287, #a6abb0 45%, #8e9398 100%); }

  .footer-name { left: 38px; top: 1067px; font-size: 32px; color: var(--blue); }
  .footer-address { left: 38px; top: 1107px; font-size: 22px; color: var(--text); }
  .globe { position: absolute; left: 725px; top: 1080px; }
  .footer-url { left: 786px; top: 1088px; font-size: 25px; color: #ffffff; }
</style>
</head>
<body>
<div class="advert">
  <svg class="frame" width="1200" height="1165" viewBox="0 0 1200 1165" aria-hidden="true">
    <rect x="0" y="0" width="623" height="11" fill="var(--blue)"/>
    <rect x="623" y="0" width="577" height="11" fill="var(--green)"/>
    <polygon points="0,11 619,11 506,151 0,151" fill="var(--ink)"/>
    <rect x="0" y="1036" width="623" height="11" fill="var(--green)"/>
    <rect x="623" y="1036" width="577" height="11" fill="var(--blue)"/>
    <polygon points="623,1047 1200,1047 1200,1161 690,1161" fill="var(--ink)"/>
    <rect x="0" y="1161" width="1200" height="4" fill="var(--blue)"/>
  </svg>

  <svg class="phone-icon" width="94" height="94" viewBox="0 0 94 94" aria-hidden="true">
    <circle cx="47" cy="47" r="43" fill="none" stroke="var(--green)" stroke-width="5"/>
    <path d="M36 24c-4 2-7 6-6 11 2 11 9 24 19 32 4 3 9 3 12 0l3-4-10-8-5 4c-5-4-9-11-11-17l5-3-4-12z" fill="none" stroke="var(--green)" stroke-width="4" stroke-linejoin="round"/>
  </svg>
  <div class="abs call-label">Call or Text</div>
  <div class="abs call-number">123.456.7890</div>

  <div class="brand-mark" aria-hidden="true"></div>
  <div class="abs brand brand-name">Brisk Rainshield</div>
  <div class="abs brand brand-sub">Roofing &amp; Façades</div>

  <h2 class="abs services-title">Our Services</h2>
  <ul class="services">
    <li><svg width="16" height="16" viewBox="0 0 16 16"><circle cx="7" cy="9" r="6" fill="none" stroke="#333" stroke-width="1.6"/><path d="M4 9l3 3 8-10" fill="none" stroke="#333" stroke-width="1.8"/></svg>Pitched (Slating &amp; Tiling)</li>
    <li><svg width="16" height="16" viewBox="0 0 16 16"><circle cx="7" cy="9" r="6" fill="none" stroke="#333" stroke-width="1.6"/><path d="M4 9l3 3 8-10" fill="none" stroke="#333" stroke-width="1.8"/></svg>Flat (Single Ply, Liquid &amp; Mineral Felt)</li>
    <li><svg width="16" height="16" viewBox="0 0 16 16"><circle cx="7" cy="9" r="6" fill="none" stroke="#333" stroke-width="1.6"/><path d="M4 9l3 3 8-10" fill="none" stroke="#333" stroke-width="1.8"/></svg>Hard Metal (Zinc Standing Seam)</li>
    <li><svg width="16" height="16" viewBox="0 0 16 16"><circle cx="7" cy="9" r="6" fill="none" stroke="#333" stroke-width="1.6"/><path d="M4 9l3 3 8-10" fill="none" stroke="#333" stroke-width="1.8"/></svg>Leadwork</li>
    <li><svg width="16" height="16" viewBox="0 0 16 16"><circle cx="7" cy="9" r="6" fill="none" stroke="#333" stroke-width="1.6"/><path d="M4 9l3 3 8-10" fill="none" stroke="#333" stroke-width="1.8"/></svg>Roof lights and lanterns</li>
  </ul>

  <div class="notes">
    <p>100% Flame Free Applications Available,<br>Eliminating All Fire Risks To Your Property<br>Expert Consultation And Advice.</p>
    <p>Product Warranty And/or Insurance<br>Backed Warranty Available.</p>
    <p>Fully Insured Contractor.</p>
  </div>

  <div class="slogan">Local Owned &amp; Operated<br>Professional Service<br>Affordable Rates</div>

  <div class="photo photo-lead" role="img" aria-label="Photo of lead flashing detail on a roof edge"><span class="photo-label">Leadwork</span></div>
  <div class="photo photo-membrane" role="img" aria-label="Photo of a roll of roofing membrane on a wet blue surface"><span class="photo-label">Membrane</span></div>
  <div class="photo photo-pitched" role="img" aria-label="Photo of a tiled pitched roof on a brick house"><span class="photo-label">Pitched Roof</span></div>
  <div class="photo photo-lantern" role="img" aria-label="Photo of a glass roof lantern on a flat roof under blue sky"><span class="photo-label">Roof Lantern</span></div>
  <div class="photo photo-zinc" role="img" aria-label="Photo of grey zinc standing seam cladding"><span class="photo-label">Zinc Standing Seam</span></div>

  <div class="abs footer-name">Brisk Rainshield</div>
  <div class="abs footer-address">Street Name, City Name State Zipcode</div>
  <svg class="globe" width="44" height="44" viewBox="0 0 44 44" aria-hidden="true">
    <g fill="none" stroke="#ffffff" stroke-width="1.8">
      <circle cx="22" cy="22" r="20"/>
      <ellipse cx="22" cy="22" rx="9" ry="20"/>
      <line x1="22" y1="2" x2="22" y2="42"/>
      <line x1="2" y1="22" x2="42" y2="22"/>
      <path d="M6 12h32M6 32h32"/>
    </g>
  </svg>
  <div class="abs footer-url">www.BriskRainshield.com</div>
</div>
</body>
</html>
```